Need Business Card for our Real Estate Business with Sales Executive's Picture

PANTONE 484 C ( RED)

PANTONE 2766 C ( BLUE

Industry/Entity Type

Real Estate

Contact Information for Business Card

Name, Mobile, email, & picture of Person
Agency Phone, address, Web address

Requirements
Must have
• Our Logo Colours, Agent Picture,

```html
<!DOCTYPE html>
<html lang="en">
<head>
<meta charset="utf-8">
<title>Dana Whitford – Business Card</title>
<link rel="stylesheet" href="https://fonts.googleapis.com/css2?family=Amaranth:wght@700&family=Open+Sans:wght@400;600&display=swap">
<style>
  :root {
    --brand-red: #9a3324;
    --brand-blue: #1b2656;
    --ink: #1e2a52;
    --card-bg: #eef0f2;
    --page-bg: #d8d5d1;
    --white: #ffffff;
  }
  html, body {
    margin: 0;
    padding: 0;
    width: 1200px;
    height: 1054px;
    overflow: hidden;
    background: var(--page-bg);
  }
  .business-card {
    position: absolute;
    left: 100px;
    top: 226px;
    width: 1000px;
    height: 602px;
    background: var(--card-bg);
    overflow: hidden;
    box-shadow: 0 10px 30px rgba(0,0,0,0.18);
    font-family: "Open Sans", Arial, sans-serif;
    color: var(--ink);
  }
  .agent-photo {
    position: absolute;
    left: 528px;
    top: 0;
    width: 472px;
    height: 575px;
    background: linear-gradient(180deg, #e9e4dc 0%, #d9cbbb 35%, #b89a85 55%, #2c3f78 75%, #1d2b5c 100%);
  }
  .header-bands,
  .footer-bands {
    position: absolute;
    left: 0;
    display: block;
  }
  .header-bands { top: 89px; }
  .footer-bands { top: 575px; }
  .agent-name {
    position: absolute;
    left: 51px;
    top: 105px;
    margin: 0;
    font-family: "Amaranth", "Trebuchet MS", sans-serif;
    font-weight: 700;
    font-size: 33px;
    line-height: 40px;
    color: var(--white);
  }
  .agent-title {
    position: absolute;
    left: 51px;
    top: 148px;
    margin: 0;
    font-size: 21px;
    line-height: 28px;
    color: var(--white);
  }
  .office-address {
    position: absolute;
    left: 51px;
    top: 302px;
    margin: 0;
    font-style: normal;
    font-size: 22px;
    line-height: 33px;
  }
  .contact-list {
    position: absolute;
    left: 51px;
    top: 385px;
    margin: 0;
    padding: 0;
    list-style: none;
    font-size: 22px;
    line-height: 32.5px;
  }
  .contact-item {
    display: flex;
    align-items: center;
    height: 32.5px;
  }
  .contact-icon {
    width: 18px;
    height: 18px;
    margin-right: 20px;
    fill: var(--brand-red);
  }
  .web-domain { color: var(--brand-red); }
</style>
</head>
<body>
  <section class="business-card">
    <div class="agent-photo" role="img" aria-label="Portrait photo of the agent in a navy suit and striped tie, smiling"></div>

    <svg class="header-bands" width="617" height="111" viewBox="0 0 617 111" aria-hidden="true">
      <polygon points="369,0 617,0 617,111 464,111" fill="var(--brand-blue)"/>
      <polygon points="0,0 369,0 464,111 0,111" fill="var(--brand-red)"/>
    </svg>

    <h1 class="agent-name">Dana Whitford</h1>
    <p class="agent-title">Managing Director</p>

    <address class="office-address">
      418 Aspen Ridge Dr #204,<br>
      Golden, CO 80401
    </address>

    <ul class="contact-list">
      <li class="contact-item">
        <svg class="contact-icon" viewBox="0 0 18 18" aria-hidden="true"><path d="M4 1h10a1 1 0 0 1 1 1v14a1 1 0 0 1-1 1H4a1 1 0 0 1-1-1V2a1 1 0 0 1 1-1zm1 2v10h8V3zm4 11a1 1 0 1 0 0 2 1 1 0 0 0 0-2z"/></svg>
        555.210.4837
      </li>
      <li class="contact-item">
        <svg class="contact-icon" viewBox="0 0 18 18" aria-hidden="true"><path d="M1 6c0-2 3-3 8-3s8 1 8 3v1h-4V5.5c-1-.4-2.4-.5-4-.5s-3 .1-4 .5V7H1zm3 2h10l2 8H2zm5 2a2 2 0 1 0 0 4 2 2 0 0 0 0-4z"/></svg>
        555-318-2290
      </li>
      <li class="contact-item">
        <svg class="contact-icon" viewBox="0 0 18 18" aria-hidden="true"><path d="M1 4h16v10H1zm1.5 1.2L9 10l6.5-4.8V5H2.5z"/></svg>
        dwhitford@mesaridgehomes.com
      </li>
      <li class="contact-item">
        <svg class="contact-icon" viewBox="0 0 18 18" aria-hidden="true"><path d="M9 1a8 8 0 1 0 0 16A8 8 0 0 0 9 1zm-1 2.2V6H5.3A6 6 0 0 1 8 3.2zm2 0A6 6 0 0 1 12.7 6H10zM3.1 8H8v2H3.1a6 6 0 0 1 0-2zM10 8h4.9a6 6 0 0 1 0 2H10zm-4.7 4H8v2.8A6 6 0 0 1 5.3 12zM10 12h2.7a6 6 0 0 1-2.7 2.8z"/></svg>
        <span>www.<span class="web-domain">mesaridgehomes</span>.com</span>
      </li>
    </ul>

    <svg class="footer-bands" width="1000" height="27" viewBox="0 0 1000 27" aria-hidden="true">
      <rect x="0" y="0" width="1000" height="27" fill="var(--brand-blue)"/>
      <polygon points="693,0 1000,0 1000,27 668,27" fill="var(--brand-red)"/>
    </svg>
  </section>
</body>
</html>
```